RESIDENTIAL CONSTRUCTION

We are a company that specializes in building custom residential homes, the design should also emphasize that quality and service is our priority.

Industry/Entity Type

Construction Company

Contact Information for Business Card

Contact Person: Marcus Lindqvist
Company Address: 273 West Alder Ave San Jose , Ca 95380
Phone Number : 408-731-2946
Email Address: Stoneridgehomes517@mailvista.net

Font styles to use
Sans Serif

Colors
ec1f27

Requirements
Must have
• CSLB # 7362015
Nice to have
• needs to have same color as logo i uploaded, we will be printing these on a clear plastic card.

```html
<!DOCTYPE html>
<html lang="en">
<head>
<meta charset="utf-8">
<title>Stoneridge Homes – Business Card</title>
<link rel="stylesheet" href="https://fonts.googleapis.com/css2?family=Oswald:wght@500&family=Lato:wght@400&display=swap">
<style>
  :root {
    --brand-red: #ec1f27;
    --name-red: #c8202a;
    --ink: #1a1a1a;
    --rule: #222222;
    --card: #ffffff;
    --backdrop: #e9e7e5;
  }
  * { box-sizing: border-box; margin: 0; padding: 0; }
  html, body {
    width: 1200px; height: 900px; overflow: hidden;
    background: var(--backdrop);
  }
  body { display: flex; align-items: center; justify-content: center; }

  .business-card {
    position: relative;
    width: 846px; height: 520px;
    background: var(--card);
    box-shadow: 0 10px 30px rgba(0,0,0,0.12);
    font-family: "Lato", Arial, sans-serif;
    color: var(--ink);
    overflow: hidden;
  }

  .brand {
    position: absolute; top: 96px; left: 0; right: 0;
    display: flex; align-items: center; justify-content: center; gap: 20px;
  }
  .brand-square {
    width: 64px; height: 64px;
    background: var(--brand-red);
  }
  .brand-name {
    font-family: "Lato", Arial, sans-serif;
    font-weight: 400;
    font-size: 54px;
    line-height: 1;
    color: var(--brand-red);
    white-space: nowrap;
  }

  .contact-name {
    position: absolute; top: 306px; left: 50px; right: 50px;
    display: flex; align-items: center; gap: 16px;
  }
  .contact-name .rule { flex: 1; height: 2px; background: var(--rule); }
  .contact-name h1 {
    font-family: "Oswald", "Arial Narrow", sans-serif;
    font-weight: 500; font-size: 28px; letter-spacing: 1.5px;
    color: var(--name-red); text-transform: uppercase;
    white-space: nowrap;
  }

  .details {
    position: absolute; top: 354px; left: 0; right: 0;
    text-align: center; font-size: 23px; line-height: 42px;
  }
  .details p { display: flex; justify-content: center; align-items: center; gap: 8px; white-space: nowrap; }
  .details .pair { gap: 28px; }
  .details .item { display: inline-flex; align-items: center; gap: 8px; }
  .details svg { fill: var(--name-red); flex: none; }

  .footer-band {
    position: absolute; left: 0; right: 0; bottom: 0;
    height: 14px; background: var(--name-red);
  }
</style>
</head>
<body>
  <article class="business-card">
    <header class="brand">
      <span class="brand-square" aria-hidden="true"></span>
      <p class="brand-name">Stoneridge Homes</p>
    </header>

    <div class="contact-name">
      <span class="rule"></span>
      <h1>Marcus Lindqvist</h1>
      <span class="rule"></span>
    </div>

    <section class="details">
      <p>CSLB # 7362015</p>
      <p>
        <svg width="14" height="20" viewBox="0 0 14 20" aria-hidden="true"><path d="M7 0C3.1 0 0 3.1 0 7c0 5 7 13 7 13s7-8 7-13c0-3.9-3.1-7-7-7zm0 9.6A2.6 2.6 0 1 1 7 4.4a2.6 2.6 0 0 1 0 5.2z"/></svg>
        273 West Alder Ave San Jose, Ca 95380
      </p>
      <p class="pair">
        <span class="item">
          <svg width="20" height="16" viewBox="0 0 20 16" aria-hidden="true"><path d="M10 2C5 2 1 3.5 0.5 5.5L0 8h4.5l1-2.5C7 5 13 5 14.5 5.5l1 2.5H20l-.5-2.5C19 3.5 15 2 10 2zM5 9l-2 6h14l-2-6H5zm5 1.2a2 2 0 1 1 0 4 2 2 0 0 1 0-4z"/></svg>
          408-731-2946
        </span>
        <span class="item">
          <svg width="18" height="13" viewBox="0 0 18 13" aria-hidden="true"><path d="M0 0h18v1.5L9 7 0 1.5z"/><path d="M0 3.3 9 8.8l9-5.5V13H0z"/></svg>
          Stoneridgehomes517@mailvista.net
        </span>
      </p>
    </section>

    <div class="footer-band"></div>
  </article>
</body>
</html>
```